American cannabis tech company business card design

Pavrel.com is seeking a modern, professional, and brand-aligned business card that represents our company and its core values: Mission, Story, Values, and Impact. As an innovative cannabis company, we want a business card that is not only visually appealing but also serves as a representation of who we are and what we stand for.

Project Scope: Design a double-sided business card that integrates our brand identity and core values. Incorporate our key brand elements, ensuring a sleek and contemporary aesthetic. Visually reflect our core values (Mission, Story, Values, Impact) in a way that is engaging yet professional.

Target Market(s)

Vendors, third parties,

Contact Information for Business Card

Contact details (name, title, email, phone, website, etc.)

Font styles to use
Other font styles liked:
• Caslon, Centra

Colors

Designer to choose colors to be used in the design.

Requirements
Must have
• Pavrel.com logo and branding A creative yet clean way to integrate our core values (Mission, Story, Values, Impact) Modern typography and a well-structured layout
Nice to have
• forest green, grey, white, black
Should not have
• references to marijuana, leafs, plants, or related product

```html
<!DOCTYPE html>
<html lang="en">
<head>
<meta charset="utf-8">
<title>Pavrel.com — Business Card</title>
<link href="https://fonts.googleapis.com/css2?family=Roboto:wght@400;700;900&display=swap" rel="stylesheet">
<style>
  :root {
    --forest: #1f4a26;
    --forest-deep: #163a1c;
    --black: #111111;
    --white: #ffffff;
    --paper: #f2f2f2;
    --stage: #d9d6cf;
    --muted: #dfe8df;
  }
  * { box-sizing: border-box; margin: 0; padding: 0; }
  html, body { width: 1200px; height: 917px; overflow: hidden; }
  body {
    background: var(--stage);
    font-family: "Roboto", Arial, sans-serif;
    position: relative;
  }
  .card {
    position: absolute;
    width: 560px;
    height: 320px;
    border-radius: 18px;
    overflow: hidden;
    box-shadow: 0 10px 28px rgba(0,0,0,.25);
  }
  /* Front */
  .card-front { left: 60px; top: 110px; background: linear-gradient(135deg, var(--white), var(--paper)); }
  .card-front .wave { position: absolute; inset: 0; width: 100%; height: 100%; }
  .front-logo {
    position: absolute; left: 30px; top: 34px;
    font-weight: 900; font-size: 62px; line-height: 1; letter-spacing: 1px;
    color: var(--forest);
  }
  .identity { position: absolute; left: 272px; top: 206px; color: var(--white); }
  .identity .name { font-weight: 700; font-size: 17px; letter-spacing: .5px; text-transform: uppercase; }
  .identity .role { font-size: 13px; color: var(--muted); margin-top: 1px; }
  .contacts { position: absolute; left: 272px; top: 254px; color: var(--white); font-size: 13px; line-height: 17px; }
  .contacts li { list-style: none; display: flex; align-items: center; gap: 7px; }
  .contacts svg { width: 13px; height: 13px; flex: none; }
  .socials { position: absolute; right: 28px; top: 40px; display: flex; gap: 8px; }
  .socials span { width: 18px; height: 18px; border-radius: 3px; background: var(--white); opacity: .9; }
  /* Back */
  .card-back { left: 580px; top: 490px; background: var(--forest); }
  .back-photo {
    position: absolute; inset: 0;
    background:
      radial-gradient(ellipse at 40% 35%, rgba(120,140,70,.55), transparent 60%),
      radial-gradient(ellipse at 75% 80%, rgba(200,210,190,.25), transparent 55%),
      linear-gradient(160deg, #2b5a2c, var(--forest-deep));
  }
  .back-brand { position: absolute; inset: 0; display: flex; flex-direction: column; align-items: center; justify-content: center; }
  .back-logo { font-weight: 900; font-size: 84px; color: var(--white); letter-spacing: 1px; }
  .back-url { font-size: 14px; letter-spacing: 3px; color: var(--white); margin-top: 2px; }
</style>
</head>
<body>
  <section class="card card-front" aria-label="Business card front">
    <svg class="wave" viewBox="0 0 560 320" preserveAspectRatio="none" aria-hidden="true">
      <path d="M0,272 C140,262 235,175 282,108 C310,66 330,24 345,0 L560,0 L560,320 L0,320 Z" fill="var(--black)"/>
      <path d="M0,294 C148,284 246,195 296,126 C326,82 346,28 364,0 L560,0 L560,320 L0,320 Z" fill="var(--white)"/>
      <path d="M0,300 C150,290 250,200 300,130 C330,85 350,30 370,0 L560,0 L560,320 L0,320 Z" fill="var(--forest)"/>
    </svg>
    <div class="front-logo">PAVREL</div>
    <div class="identity">
      <div class="name">Daniel R. Hale</div>
      <div class="role">Director</div>
    </div>
    <ul class="contacts">
      <li><svg viewBox="0 0 16 16"><rect width="16" height="16" rx="3" fill="#fff"/><path d="M5 3.5l2 2-1 1.3c.6 1.3 1.6 2.3 2.9 2.9l1.3-1 2 2-1.2 1.8C7.6 12.3 3.7 8.4 3.5 4.7z" fill="var(--forest)"/></svg>+1 405-555-0148</li>
      <li><svg viewBox="0 0 16 16"><rect width="16" height="16" rx="3" fill="#fff"/><rect x="3" y="4.5" width="10" height="7" fill="none" stroke="var(--forest)" stroke-width="1.3"/><path d="M3 4.5l5 4 5-4" fill="none" stroke="var(--forest)" stroke-width="1.3"/></svg>team@pavrel.com</li>
      <li><svg viewBox="0 0 16 16"><rect width="16" height="16" rx="3" fill="#fff"/><circle cx="8" cy="8" r="4.8" fill="none" stroke="var(--forest)" stroke-width="1.2"/><path d="M3.2 8h9.6M8 3.2c-2.4 3-2.4 6.6 0 9.6M8 3.2c2.4 3 2.4 6.6 0 9.6" fill="none" stroke="var(--forest)" stroke-width="1"/></svg>www.PAVREL.com</li>
    </ul>
    <div class="socials" aria-label="Social profiles"><span></span><span></span><span></span></div>
  </section>

  <section class="card card-back" aria-label="Business card back">
    <div class="back-photo" role="img" aria-label="Green-toned lifestyle photograph background"></div>
    <div class="back-brand">
      <div class="back-logo">PAVREL</div>
      <div class="back-url">www.PAVREL.com</div>
    </div>
  </section>
</body>
</html>
```